One Pager Fact Sheet Design

I need a couple of headers and footer designed to use for information security fact sheets to give to customers. Similar to the one listed below.

```html
<!DOCTYPE html>
<html lang="en">
<head>
<meta charset="utf-8">
<title>Security Fact Sheet – Headers and Footer</title>
<link href="https://fonts.googleapis.com/css2?family=Exo+2:wght@800&family=Open+Sans:wght@400;600&display=swap" rel="stylesheet">
<style>
  :root {
    --page: #ffffff;
    --sheet: #f4efef;
    --red: #e31e24;
    --red-dark: #b8141a;
    --red-light: #f0353a;
    --white: #ffffff;
    --footer-bg: #e0e0e0;
    --ink: #1a1a1a;
    --social: #1f78c8;
  }
  * { margin: 0; padding: 0; box-sizing: border-box; }
  html, body { width: 1200px; height: 665px; overflow: hidden; background: var(--page); }
  .sheet {
    position: absolute; left: 30px; top: 0; width: 1137px; height: 648px;
    background: var(--sheet);
  }
  .banner { position: absolute; left: 43px; width: 1114px; overflow: hidden; background: var(--red); }
  .banner svg.banner-art { position: absolute; inset: 0; width: 100%; height: 100%; }
  .banner-large { top: 18px; height: 238px; }
  .banner-slim { top: 364px; height: 97px; }

  .brand { position: absolute; display: flex; align-items: center; color: var(--white);
    font-family: "Exo 2", sans-serif; font-weight: 800; letter-spacing: -0.5px; }
  .brand-dot { border: 5px solid var(--white); border-radius: 50%; flex: none; }
  .banner-large .brand { left: 66px; top: 105px; font-size: 52px; gap: 14px; }
  .banner-large .brand-dot { width: 64px; height: 64px; border-width: 7px; }
  .banner-slim .brand { left: 43px; top: 26px; font-size: 32px; gap: 10px; }
  .banner-slim .brand-dot { width: 42px; height: 42px; }
  .center-mark { position: absolute; left: 628px; top: 26px; width: 44px; height: 44px;
    border: 5px solid var(--white); border-radius: 50%; }

  .footer-rule { position: absolute; left: 43px; top: 523px; width: 1114px; height: 5px; background: var(--red); }
  .footer { position: absolute; left: 43px; top: 528px; width: 1114px; height: 94px;
    background: var(--footer-bg); display: flex; align-items: center; padding-left: 36px;
    font-family: "Open Sans", sans-serif; font-size: 15px; color: var(--ink); }
  .contact { display: flex; align-items: center; gap: 6px; margin-right: 12px; white-space: nowrap; }
  .contact-icon { width: 22px; height: 22px; border-radius: 50%; background: var(--red);
    display: flex; align-items: center; justify-content: center; flex: none; }
  .contact-icon svg { width: 13px; height: 13px; }
  .contact.phone { margin-left: 6px; margin-right: 14px; }
  .divider { width: 3px; height: 28px; background: var(--red); margin-right: 14px; }
  .social { display: flex; gap: 7px; margin-right: 9px; }
  .social span { width: 22px; height: 22px; border-radius: 50%; background: var(--social); }
</style>
</head>
<body>
<div class="sheet"></div>

<header class="banner banner-large">
  <svg class="banner-art" viewBox="0 0 1114 238" preserveAspectRatio="none">
    <polygon points="0,0 240,0 0,200" fill="var(--red-dark)" opacity="0.45"/>
    <polygon points="0,60 180,238 0,238" fill="var(--red-dark)" opacity="0.35"/>
    <polygon points="230,0 520,0 420,238 180,238" fill="var(--red-dark)" opacity="0.18"/>
    <polygon points="600,0 760,0 640,238 470,238" fill="var(--red-light)" opacity="0.5"/>
    <polygon points="700,0 822,0 737,238 610,238" fill="var(--red)"/>
    <polygon points="822,0 1114,0 1114,238 737,238" fill="url(#photoLarge)" role="img" aria-label="Photo of an audience at a security seminar with a glowing padlock overlay"/>
    <defs>
      <radialGradient id="photoLarge" cx="0.72" cy="0.45" r="0.7">
        <stop offset="0" stop-color="#ff4a4a"/>
        <stop offset="0.45" stop-color="#c0161c"/>
        <stop offset="1" stop-color="#2a0505"/>
      </radialGradient>
    </defs>
  </svg>
  <div class="brand"><span class="brand-dot"></span>vaultline</div>
</header>

<header class="banner banner-slim">
  <svg class="banner-art" viewBox="0 0 1114 97" preserveAspectRatio="none">
    <polygon points="360,0 470,0 400,97 295,97" fill="var(--red-dark)" opacity="0.45"/>
    <polygon points="470,0 620,0 540,97 400,97" fill="var(--red-dark)" opacity="0.2"/>
    <polygon points="780,0 902,0 875,97 760,97" fill="var(--red-light)" opacity="0.5"/>
    <polygon points="902,0 1114,0 1114,97 875,97" fill="url(#photoSlim)" role="img" aria-label="Photo of an audience at a security seminar with a glowing padlock overlay"/>
    <defs>
      <radialGradient id="photoSlim" cx="0.65" cy="0.5" r="0.7">
        <stop offset="0" stop-color="#ff4a4a"/>
        <stop offset="0.45" stop-color="#c0161c"/>
        <stop offset="1" stop-color="#2a0505"/>
      </radialGradient>
    </defs>
  </svg>
  <div class="brand"><span class="brand-dot"></span>vaultline</div>
  <span class="center-mark"></span>
</header>

<div class="footer-rule"></div>
<footer class="footer">
  <div class="contact">
    <span class="contact-icon"><svg viewBox="0 0 16 16" fill="none" stroke="#fff" stroke-width="1.6"><circle cx="8" cy="8" r="6.5"/><ellipse cx="8" cy="8" rx="2.8" ry="6.5"/><line x1="1.5" y1="8" x2="14.5" y2="8"/></svg></span>
    vaultline.in&nbsp; vaultline-secure.org
  </div>
  <div class="contact">
    <span class="contact-icon"><svg viewBox="0 0 16 16"><polygon points="2,2 14,7 9,9 7,14" fill="#fff"/></svg></span>
    profile.example/company/vaultline-secure
  </div>
  <div class="contact phone">
    <span class="contact-icon"><svg viewBox="0 0 16 16"><path d="M2 6 Q8 1 14 6 L12 8 L10 6.5 L6 6.5 L4 8 Z M4 9 H12 V13 H4 Z" fill="#fff"/></svg></span>
    01632 960 481
  </div>
  <span class="divider"></span>
  <div class="social"><span></span><span></span><span></span><span></span></div>
  <div class="contact">@vaultline-secure.org</div>
</footer>
</body>
</html>
```